Business Card Design - VNT (company name)

Over 20 years of progressive technology design, migration and management experience that drives business objectives and streamlines operations. Continuously challenge conventions to meet and exceed business security, availability and functionality requirements. Maintain exceptional vendor relationships to ensure ongoing knowledge of emerging products and to secure preferred service agreements. Recruit and utilize top talent and foster a collegial environment that advances innovation and performance excellence. design logo using 3 arrows of different colors green, gold, blue

Industry/Entity Type

Progressive

Contact Information for Business Card

Martin K. Osgood
IT Strategist / Consultant

626.583.2907 MOsgood@vntosgood.example 4817 Brenning Court Pasadena, CA 91104

Colors
0255a3
f37122
fece3e

Requirements
Must have
• Note NEW EMAIL ADDRESS
• MOsgood@vntosgood.example
• NOTE NEW ORDER of the work I do.
• Infrastructure – Systems – Cybersecurity
Nice to have
• main color should be orange

```html
<!DOCTYPE html>
<html lang="en">
<head>
<meta charset="utf-8">
<title>VNT – Business Card</title>
<link href="https://fonts.googleapis.com/css2?family=Raleway:wght@300;400;700&display=swap" rel="stylesheet">
<style>
  :root {
    --stage: #d6d6d6;
    --card: #2e3034;
    --card-edge: #26282b;
    --orange: #f37122;
    --blue: #0255a3;
    --gold: #fece3e;
    --ink-light: #ffffff;
    --ink-muted: #b9bbbf;
    --ink-contact: #d8d9dc;
  }
  * { margin: 0; padding: 0; box-sizing: border-box; }
  html, body {
    width: 1200px;
    height: 900px;
    overflow: hidden;
  }
  body {
    background: var(--stage);
    font-family: "Raleway", sans-serif;
    position: relative;
  }
  .card {
    position: absolute;
    background: var(--card);
    border-radius: 18px;
    box-shadow: 0 0 0 1px var(--card-edge);
  }
  .card--front {
    left: 322px; top: 70px;
    width: 580px; height: 337px;
    display: flex;
    align-items: center;
    justify-content: center;
  }
  .card--back {
    left: 322px; top: 466px;
    width: 575px; height: 336px;
  }
  .brand-name {
    font-family: "Raleway", sans-serif;
    font-weight: 700;
    color: var(--orange);
    letter-spacing: 0.04em;
    line-height: 1;
  }
  .card--front .brand-name {
    font-size: 120px;
    margin-top: -10px;
  }
  .card--back .brand-name {
    position: absolute;
    left: 88px;
    top: 120px;
    width: 180px;
    text-align: center;
    font-size: 62px;
  }
  .identity {
    position: absolute;
    left: 301px;
    top: 114px;
  }
  .identity__name {
    font-size: 30px;
    font-weight: 300;
    color: var(--ink-light);
    line-height: 1.1;
    white-space: nowrap;
  }
  .identity__name .surname {
    color: var(--ink-muted);
  }
  .identity__role {
    font-size: 15px;
    font-weight: 400;
    color: var(--orange);
    margin-top: 4px;
    white-space: nowrap;
  }
  .identity__services {
    font-size: 12px;
    font-weight: 400;
    color: var(--ink-muted);
    margin-top: 3px;
    white-space: nowrap;
  }
  .contact {
    list-style: none;
    margin-top: 14px;
    margin-left: 4px;
    font-size: 15px;
    font-weight: 400;
    color: var(--ink-contact);
    line-height: 20px;
    white-space: nowrap;
  }
</style>
</head>
<body>
  <section class="card card--front" aria-label="Card front">
    <span class="brand-name">VNT</span>
  </section>

  <section class="card card--back" aria-label="Card back">
    <span class="brand-name">VNT</span>
    <div class="identity">
      <h1 class="identity__name">Martin <span class="surname">K. Osgood</span></h1>
      <p class="identity__role">IT Strategist / Consultant</p>
      <p class="identity__services">Infrastructure – Systems – Cybersecurity</p>
      <ul class="contact">
        <li class="contact__email">MOsgood@vntosgood.example</li>
        <li class="contact__phone">626.583.2907</li>
      </ul>
    </div>
  </section>
</body>
</html>
```